Simple Postcard Design

We want to have Prenta do a mailing for our new real estate company. We have roughed a sketch of what we would like. A picture of the property on one side and the copy on the reverse side.Attached are the files.

POSTCARD Size-8.52" x 5.47" **********

Target Market(s)

Residents of our town

Industry/Entity Type

Real Estate

Font styles to use
Serif

Colors
00a990

Requirements
Must have
• Look of elegance
Nice to have
• NO NO Border on picture,,,,,banner on 45 in top left corner
• "New Listing"

```html
<!DOCTYPE html>
<html lang="en">
<head>
<meta charset="utf-8">
<title>Vista Realtors – New Listing Postcard</title>
<link rel="stylesheet" href="https://fonts.googleapis.com/css2?family=Tinos:ital,wght@0,400;0,700;1,400&display=swap">
<style>
  :root {
    --page: #ecebe8;
    --card: #ffffff;
    --teal: #14a98e;
    --teal-dark: #0b7a66;
    --ink: #1a1a1a;
    --forest: #0f5130;
    --rule: #b9b9b9;
    --water: #1b2a33;
    --sand: #cdbf9f;
  }
  * { margin: 0; padding: 0; box-sizing: border-box; }
  html, body {
    width: 918px; height: 1200px; overflow: hidden;
    background: var(--page);
    font-family: "Tinos", "Times New Roman", serif;
    color: var(--ink);
  }
  .canvas { position: relative; width: 918px; height: 1200px; }

  /* Front of postcard */
  .postcard-front {
    position: absolute; left: 63px; top: 55px;
    width: 712px; height: 512px;
    background: var(--card);
    box-shadow: 0 2px 6px rgba(0,0,0,.18);
  }
  .property-photo {
    position: absolute; left: 13px; top: 13px;
    width: 686px; height: 485px;
    background:
      radial-gradient(ellipse at 45% 65%, var(--sand) 0%, #a9a27f 22%, transparent 45%),
      linear-gradient(135deg, #23343c 0%, var(--water) 40%, #3a4a3a 60%, #4d5b45 100%);
  }
  .listing-banner {
    position: absolute; left: 0; top: 32px;
    width: 236px; height: 76px;
  }
  .listing-banner svg { position: absolute; inset: 0; }
  .listing-banner span {
    position: absolute; left: 40px; top: 18px;
    font-size: 31px; color: #fff; letter-spacing: .2px;
  }

  /* Back of postcard */
  .postcard-back {
    position: absolute; left: 128px; top: 613px;
    width: 712px; height: 512px;
    background: var(--card);
    box-shadow: 0 2px 6px rgba(0,0,0,.18);
  }
  .brand {
    position: absolute; left: 37px; top: 45px;
    display: flex; align-items: center; gap: 12px;
    font-size: 30px; color: var(--forest);
  }
  .brand-square { width: 22px; height: 22px; background: var(--forest); }
  .contact {
    position: absolute; left: 37px; top: 137px;
    font-size: 15px; line-height: 17px;
  }
  .description {
    position: absolute; left: 37px; top: 232px; width: 324px;
    font-size: 15.6px; line-height: 19px;
    text-align: justify; hyphens: manual;
  }
  .disclaimer {
    position: absolute; left: 37px; top: 398px; width: 336px;
    font-size: 12px; line-height: 17px; font-style: italic;
  }
  .stamp-box {
    position: absolute; left: 599px; top: 27px;
    width: 91px; height: 61px;
    border: 1px solid var(--rule);
  }
  .address-lines {
    position: absolute; left: 450px; top: 176px; width: 240px;
  }
  .address-lines div {
    height: 1px; background: var(--rule); margin-bottom: 28px;
  }
</style>
</head>
<body>
<div class="canvas">

  <section class="postcard-front">
    <div class="property-photo" role="img" aria-label="Aerial photograph of a waterfront estate on a lagoon point, with a large shingled house, pool, sandy lot, docks and neighbouring homes"></div>
    <div class="listing-banner">
      <svg width="236" height="76" viewBox="0 0 236 76">
        <polygon points="0,62 12,62 12,76" fill="var(--teal-dark)"/>
        <polygon points="0,0 226,0 236,36 226,72 0,62" fill="var(--teal)"/>
        <line x1="0" y1="4" x2="224" y2="4" stroke="#fff" stroke-width="1"/>
        <line x1="0" y1="58" x2="224" y2="67" stroke="#fff" stroke-width="1"/>
      </svg>
      <span>New Listing</span>
    </div>
  </section>

  <section class="postcard-back">
    <div class="brand"><div class="brand-square"></div>Vista Realtors</div>

    <address class="contact" style="font-style:normal">
      VISTA REALTORS<br>
      14 Harbor Lane<br>
      Prenta, NJ 08700<br>
      555 010-4400<br>
      www.VistaRealtors.com
    </address>

    <p class="description">
      This unique 1.68 acre estate in Prenta has 644' of water front. The 22 room house features a 2 story master suite, 6 guest bed&shy;rooms, large living room, great room with 2 fireplaces, in law Suite, 15 car garage, in ground pool, brick patio, numerous porches and a 200' Dock.<br>
      Priced at $4,995,000
    </p>

    <p class="disclaimer">
      If your property is listed with a real estate broker, please disregard. It is not our intention to solicit the offerings of other real estate brokers.
    </p>

    <div class="stamp-box"></div>
    <div class="address-lines"><div></div><div></div><div></div><div></div><div></div></div>
  </section>

</div>
</body>
</html>
```